Summer Music/Chorus/Choir Camp for Young Singers Ages 8-13

We need a flyer for a summer camp for young singers ages 8-13. We are nonprofit community children's chorus in Miami, FL. Our camp provides specialized training in music theory, sight-reading,and aural training through daily choral rehearsals in an environment that is both positive and a lot of fun! Our camp offers children the opportunity to come as they are, no matter the level of experience, and grow tremendously in their musicianship skills. In addition to this, our campers participate in song-writing, masterclasses, community performances, and media projects. The final design should be clean, fun, not too crowded, should appeal to boys and girls ages 8-13, and something someone that age would consider "cool" and not too childish. Drawings are cool, something different.
Updates

Target Market(s)

Ages 8-13 and parents of those kids.

Industry/Entity Type

Community

Requirements
Must have
• All info attached.
Nice to have
• Things that relate to music, especially related to singing/choirs
Should not have
• instruments, stock photos of children, or photos from our website (unless they are used very creatively), or photos in general. I've attached our previous camp flyer and our current organization flyer but I don't necessarily want this flyer to look like those.

```html
<!DOCTYPE html>
<html lang="en">
<head>
<meta charset="utf-8">
<title>Summer Choral Camp – Bright Notes Youth Chorus</title>
<link rel="stylesheet" href="https://fonts.googleapis.com/css2?family=Bevan&family=Francois+One&family=Nunito:wght@400;600;800;900&display=swap">
<style>
  :root {
    --stage: #3b3b3d;
    --paper: #f7f7f8;
    --paper-shade: #e9eaec;
    --pink: #e1167f;
    --teal: #1f9aa6;
    --mint: #4fc7b0;
    --blue: #1b7db2;
    --sky: #2b8fc4;
    --navy: #1d4f88;
    --badge: #d9dcdf;
    --ink: #1a1a1a;
  }
  * { box-sizing: border-box; margin: 0; padding: 0; }
  html, body { width: 1200px; height: 1200px; overflow: hidden; }
  body { background: var(--stage); position: relative; font-family: "Nunito", sans-serif; }

  .flyer {
    position: absolute; left: 200px; top: 33px; width: 800px; height: 1134px;
    background: radial-gradient(ellipse at 50% 40%, var(--paper) 55%, var(--paper-shade) 100%);
    overflow: hidden;
  }
  .flyer > * { position: absolute; }

  .brand { left: 70px; top: 90px; width: 300px; color: var(--teal); font-weight: 800; font-size: 36px; line-height: 1.05; display: flex; align-items: center; gap: 14px; }
  .brand-dot { width: 26px; height: 26px; border-radius: 50%; background: var(--teal); flex: none; }

  .dates { right: 47px; top: 52px; text-align: right; color: var(--teal); font-family: "Francois One", sans-serif; }
  .dates-range { font-size: 52px; line-height: 1.05; }
  .dates-hours { font-size: 29px; line-height: 1.2; }

  .invite { right: 47px; top: 208px; text-align: right; color: var(--blue); font-weight: 800; font-size: 22px; line-height: 30px; }

  .title { left: 57px; top: 292px; color: var(--pink); font-family: "Bevan", serif; font-weight: 400; font-size: 50px; line-height: 64px; letter-spacing: 2px; }

  .price { right: 47px; top: 322px; text-align: right; font-family: "Francois One", sans-serif; }
  .price-cost { color: var(--pink); font-size: 34px; line-height: 42px; }
  .price-session { color: var(--teal); font-size: 30px; line-height: 38px; }
  .price-note { color: var(--teal); font-family: "Nunito", sans-serif; font-size: 13px; font-weight: 600; margin-top: 4px; }

  .illustration { left: 33px; top: 420px; width: 767px; height: 440px; }

  .details { left: 60px; top: 850px; }
  .details-label { color: var(--pink); font-weight: 900; font-size: 21px; line-height: 28px; }
  .details-address { color: var(--sky); font-size: 21px; line-height: 31px; margin-bottom: 8px; }
  .details-contact { color: var(--navy); font-size: 19px; line-height: 28px; font-weight: 800; }
  .details-contact .web { font-weight: 600; }

  .partner { left: 520px; top: 920px; width: 280px; height: 190px; background: #ffffff; }
  .access-icons { position: absolute; left: 18px; bottom: 34px; }
  .partner-badge { position: absolute; right: 40px; top: 40px; width: 100px; height: 100px; background: var(--badge); }

  .footnote { left: 0; right: 0; top: 1108px; text-align: center; color: var(--blue); font-size: 11.5px; font-weight: 600; }
</style>
</head>
<body>
  <main class="flyer">
    <div class="brand"><span class="brand-dot"></span><span>Bright Notes Youth Chorus</span></div>

    <div class="dates">
      <div class="dates-range">July 18-29</div>
      <div class="dates-hours">9am-3pm (M-F)</div>
    </div>

    <p class="invite">Calling All Boys And Girls<br>In Grades 3 Through 9<br>Who Love To Sing!</p>

    <h1 class="title">Summer<br>Choral Camp</h1>

    <div class="price">
      <div class="price-cost">COST- *$300</div>
      <div class="price-session">FOR 2-WEEK SESSION</div>
      <div class="price-note">*PRICE DOES NOT INCLUDE LUNCH</div>
    </div>

    <svg class="illustration" role="img" aria-label="Illustration of a large teal treble clef with a flowing staff bursting into colourful music notes" viewBox="0 0 767 440">
      <defs>
        <linearGradient id="notesTone" x1="0" y1="1" x2="1" y2="0">
          <stop offset="0" stop-color="#4fc7b0"/>
          <stop offset="0.45" stop-color="#f6c23a"/>
          <stop offset="0.75" stop-color="#e1167f"/>
          <stop offset="1" stop-color="#3aa7e0"/>
        </linearGradient>
      </defs>
      <path d="M20 300 C 160 260, 300 140, 460 120 S 700 40, 767 20 L 767 250 C 650 300, 540 400, 420 430 S 120 420, 20 380 Z" fill="url(#notesTone)" opacity="0.55"/>
    </svg>

    <div class="details">
      <div class="details-label">LOCATION</div>
      <div class="details-address">Coral Bay Arts Hall<br>4820 SW 150th Avenue<br>Miami, FL 33185</div>
      <div class="details-label">CONTACT</div>
      <div class="details-contact">786.555.0142<br>hello@brightnoteschorus.org<br><span class="web">www.brightnoteschorus.org</span></div>
    </div>

    <div class="partner">
      <svg class="access-icons" width="96" height="48" viewBox="0 0 96 48" aria-label="Accessibility icons">
        <g fill="none" stroke="#111" stroke-width="4" stroke-linecap="round">
          <circle cx="22" cy="8" r="4" fill="#111" stroke="none"/>
          <path d="M20 16 L18 30 L32 30 L38 42"/>
          <path d="M14 24 A11 11 0 1 0 30 40"/>
          <path d="M66 34 C 60 30, 60 14, 72 12 C 82 12, 84 24, 76 28 C 72 30, 72 36, 68 40"/>
          <path d="M86 10 A14 14 0 0 1 88 30" stroke-width="2" stroke-dasharray="2 3"/>
        </g>
      </svg>
      <div class="partner-badge" role="img" aria-label="Venue partner badge"></div>
    </div>

    <p class="footnote">Bright Notes Youth Chorus is a 501 (c)(3) nonprofit organization. Donations made to BNYC are tax-exempt.</p>
  </main>
</body>
</html>
```